Bramwell Corner Sports Pub. Where the locals go!!

We are creating a sports pub. We are needing a fun website that offers our menu along with an event page and general info. We have some attached links that we really like:
https://www.dunmorrows.example/
https://www.cafepelindra.example/
https://www.quillstoneyx.example/
We are doing a pirate theme but that is because the area we are in. We would like to see a pirate like in our logo doing something like drinking real time similar to the dunmorrows website above.
Target Market(s)
Sports Fans
Industry/Entity Type
Pub, Bar, Restaurant
Coding
Coded - Design and coding required
Number of Pages Required
3 page
Font styles to use
Other font styles liked:
- see uploads
Look and feel

```html
<!DOCTYPE html>
<html lang="en">
<head>
<meta charset="utf-8">
<title>Bramwell Corner Sports Pub</title>
<link href="https://fonts.googleapis.com/css2?family=Rye&family=Roboto:wght@400;500;700&display=swap" rel="stylesheet">
<style>
:root{
  --green:#3f5b2c;
  --green-dark:#2f4520;
  --cream:#fdf8e3;
  --rust:#a0582a;
  --rust-deep:#8a4a22;
  --ink:#1b1b1b;
  --text:#555;
  --black:#0b0b0b;
  --white:#fff;
}
*{box-sizing:border-box;margin:0;padding:0}
html,body{width:1200px;height:4019px;overflow:hidden}
body{background:var(--cream);font-family:"Roboto",Arial,sans-serif;color:var(--ink);position:relative}
.abs{position:absolute}
.display{font-family:"Rye",Georgia,serif;letter-spacing:2px}
.top-bar{top:0;left:0;width:1200px;height:27px;background:var(--green);color:var(--white);font-size:12px;display:flex;justify-content:center;gap:70px;align-items:center}
.top-bar span{display:flex;align-items:center;gap:6px}
.nav{top:27px;left:0;width:1200px;height:59px;background:var(--cream);z-index:3}
.nav a{position:absolute;top:22px;font-size:13px;font-weight:500;color:var(--ink);text-decoration:none}
.nav a.active{color:var(--rust)}
.brand{left:545px;top:32px;width:110px;height:110px;border-radius:50%;background:var(--cream);border:3px solid var(--white);box-shadow:0 2px 6px rgba(0,0,0,.2);display:flex;align-items:center;justify-content:center;text-align:center;font-size:12px;font-weight:700;color:var(--rust-deep);line-height:1.25;padding:14px;z-index:4}
.hero{top:86px;left:0;width:1200px;height:540px;background:radial-gradient(ellipse at 60% 45%,#b08a3c 0%,#6b5228 35%,#2f2a1e 75%,#1d1c16 100%)}
.hero h1{position:absolute;left:143px;top:140px;font-size:40px;color:var(--white);font-weight:400}
.hero p{position:absolute;left:143px;top:206px;width:480px;font-size:19px;line-height:28px;color:var(--white);font-weight:500}
.btn{display:flex;align-items:center;justify-content:center;gap:8px;background:var(--green);color:var(--white);font-weight:700;font-size:15px;border:2px solid var(--green);outline:2px solid var(--white);outline-offset:-6px}
.hero .btn{position:absolute;left:145px;top:289px;width:138px;height:46px}
.tear{position:absolute;left:0;width:1200px;height:24px}
.about-frame{left:148px;top:702px;width:445px;height:351px;background:var(--rust);padding:30px 22px}
.about-frame .photo{width:100%;height:100%;background:linear-gradient(135deg,#2c3a2a,#6e5a44 45%,#9b6b52 70%,#332a24)}
.section-title{font-size:34px;text-align:center;color:var(--ink);font-weight:400}
.about-title{left:653px;top:732px;width:402px}
.about-text{left:652px;top:796px;width:403px;font-size:13px;line-height:21.5px;color:var(--text);text-align:center}
.about .btn{position:absolute;left:775px;top:975px;width:158px;height:55px}
.band{left:0;width:1200px;background:linear-gradient(180deg,#a65e2e,#98532a 50%,#a35c2c)}
.menu-band{top:1136px;height:588px}
.menu-title{top:52px;left:0;width:1200px;color:var(--cream)}
.dish{position:absolute;border-radius:50%;border:3px solid var(--white)}
.dish-label{position:absolute;width:180px;text-align:center;color:var(--white);font-size:16px;font-weight:500}
.menu-desc{left:480px;top:433px;width:240px;text-align:center;color:var(--white);font-size:13px;line-height:21px}
.dots{left:575px;top:524px;display:flex;gap:7px}
.dots i{width:11px;height:11px;border-radius:50%;border:1.5px solid var(--white);display:block}
.dots i.on{background:var(--green);width:14px;height:14px;margin-top:-1.5px}
.blog-title{top:1830px;left:0;width:1200px}
.card{top:1902px;width:289px;height:356px;background:var(--white);box-shadow:0 2px 8px rgba(0,0,0,.08)}
.card .photo{height:193px}
.card .date{position:absolute;left:20px;top:180px;background:var(--green);color:var(--white);font-size:12px;padding:6px 10px}
.card h3{position:absolute;left:20px;top:230px;width:255px;font-size:15px;line-height:23px;font-weight:700}
.card p{position:absolute;left:20px;top:290px;width:255px;font-size:13px;line-height:22px;color:var(--text)}
.testi-band{top:2340px;height:445px}
.testi-title{top:58px;left:0;width:1200px;color:var(--cream)}
.quote{position:absolute;top:125px;font-family:"Rye",Georgia,serif;font-size:44px;line-height:1;color:var(--cream)}
.tcard{position:absolute;top:137px;width:289px;height:192px;background:var(--green);border-radius:6px;padding:36px 25px 0;color:var(--white);font-size:11.5px;line-height:17.5px;text-align:justify;text-align-last:center}
.author{position:absolute;top:347px;display:flex;align-items:center;gap:8px;color:var(--white);font-size:13px;font-weight:500}
.author i{width:30px;height:30px;border-radius:50%;background:#c9b9a4;border:2px solid var(--white);display:block}
.gallery-title{top:2886px;left:0;width:1200px}
.gtile{width:216px;height:164px}
.contact{top:3393px;left:0;width:1200px;height:626px;background:var(--black);color:var(--white)}
.contact-title{top:86px;left:0;width:1200px;color:var(--white)}
.info{position:absolute;top:150px;display:flex;gap:16px;align-items:flex-start;font-size:13px;line-height:19px}
.info b{font-size:14px;display:block;margin-bottom:2px}
.field{position:absolute;background:var(--white);color:#888;font-size:12px;padding:16px 18px 0;border-radius:3px}
.contact .btn{position:absolute;left:505px;top:464px;width:188px;height:43px}
.foot-line{top:546px;left:144px;width:911px;height:1px;background:#444}
.copy{top:570px;left:144px;font-size:13px}
.foot-brand{top:550px;left:555px;width:90px;height:70px;text-align:center;font-size:11px;font-weight:700;color:var(--cream);line-height:1.3;padding-top:12px}
.social{top:566px;left:891px;display:flex;gap:14px}
.social i{width:32px;height:28px;background:var(--rust);display:block}
</style>
</head>
<body>

<svg width="0" height="0" class="abs" aria-hidden="true">
  <defs>
    <polygon id="edge" points="0,14 30,9 45,16 70,8 95,15 120,6 150,13 175,10 190,17 220,7 250,14 275,9 300,16 330,8 360,13 385,6 410,15 440,9 470,16 495,7 520,12 550,9 575,17 600,8 630,14 655,6 680,13 710,10 735,16 760,7 790,14 815,9 840,16 870,8 900,13 925,6 950,15 980,10 1005,16 1030,7 1060,14 1085,9 1110,16 1140,8 1170,13 1200,9 1200,24 0,24"/>
  </defs>
</svg>

<div class="abs top-bar">
  <span><svg width="12" height="12" viewBox="0 0 24 24" fill="#fff"><path d="M6.6 10.8a15 15 0 0 0 6.6 6.6l2.2-2.2c.3-.3.7-.4 1-.2 1.1.4 2.3.6 3.6.6.6 0 1 .4 1 1V20c0 .6-.4 1-1 1A17 17 0 0 1 3 4c0-.6.4-1 1-1h3.5c.6 0 1 .4 1 1 0 1.3.2 2.5.6 3.6.1.3 0 .7-.2 1z"/></svg>+1 888 888 8888</span>
  <span><svg width="14" height="11" viewBox="0 0 24 18" fill="none" stroke="#fff" stroke-width="2"><rect x="1" y="1" width="22" height="16"/><path d="M1 1l11 9 11-9"/></svg>info@Bramwell Corner Sports Pub.com</span>
</div>

<nav class="abs nav">
  <a class="active" style="left:143px">HOME</a>
  <a style="left:223px">ABOUT US</a>
  <a style="left:331px">BLOG</a>
  <a style="left:774px">REVIEWS</a>
  <a style="left:873px">GALLERY</a>
  <a style="left:970px">CONTACT US</a>
</nav>
<div class="abs brand">Bramwell Corner Sports Pub</div>

<header class="abs hero" role="img" aria-label="Two hands clinking frothy beer mugs in a bar">
  <h1 class="display">BRAMWELL CORNER SPORTS PUB</h1>
  <p>Lorem ipsum dolor sit amet, consectetur adipiscing elit, sed do eiusmod tempor incididunt</p>
  <div class="btn">Shop Now <svg width="13" height="13" viewBox="0 0 16 16"><circle cx="8" cy="8" r="7.5" fill="#fff"/><path d="M6 4.5 9.5 8 6 11.5" stroke="#3f5b2c" stroke-width="2" fill="none"/></svg></div>
</header>
<svg class="tear" style="top:604px" viewBox="0 0 1200 24" preserveAspectRatio="none" aria-hidden="true"><use href="#edge" fill="#fdf8e3"/></svg>

<section class="about">
  <div class="abs about-frame"><div class="photo" role="img" aria-label="Excited fans cheering in a sports bar in front of screens"></div></div>
  <h2 class="abs section-title display about-title">ABOUT US</h2>
  <p class="abs about-text">Lorem ipsum dolor sit amet, consectetur adipiscing elit, sed do eiusmod tempor incididunt ut labore et dolore magna aliqua. Ut enim ad minim veniam, quis nostrud exercitation ullamco laboris nisi ut aliquip ex ea commodo consequat. Duis aute irure dolor in reprehenderit in voluptate velit esse cillum dolore eu fugiat nulla pariatur. Excepteur sint occaecat cupidatat non proident, sunt in culpa qui officia deserunt mollit anim id est laborum.</p>
  <div class="btn">Learn More <svg width="13" height="13" viewBox="0 0 16 16"><circle cx="8" cy="8" r="7.5" fill="#fff"/><path d="M6 4.5 9.5 8 6 11.5" stroke="#3f5b2c" stroke-width="2" fill="none"/></svg></div>
</section>

<section class="abs band menu-band">
  <svg class="tear" style="top:-12px;transform:scaleY(-1)" viewBox="0 0 1200 24" preserveAspectRatio="none" aria-hidden="true"><use href="#edge" fill="#fdf8e3"/></svg>
  <h2 class="abs section-title display menu-title">OUR MENU</h2>
  <div class="dish" style="left:145px;top:151px;width:176px;height:176px;background:radial-gradient(circle,#e0a93a,#6b4a2a 70%)" role="img" aria-label="Pint of lager on a bar table"></div>
  <div class="dish" style="left:333px;top:151px;width:176px;height:176px;background:radial-gradient(circle,#b0672a,#9a9a9a 60%,#eee)" role="img" aria-label="Beer bottle on ice"></div>
  <div class="dish" style="left:693px;top:151px;width:176px;height:176px;background:radial-gradient(circle,#7a3a1a,#4a2a18 70%)" role="img" aria-label="Two glasses of dark ale"></div>
  <div class="dish" style="left:877px;top:151px;width:176px;height:176px;background:radial-gradient(circle,#d8344a,#c9c9c9 70%)" role="img" aria-label="Red cocktails being poured"></div>
  <div class="dish" style="left:493px;top:145px;width:214px;height:214px;background:radial-gradient(circle,#e6b84a,#5a3a18 70%);z-index:2" role="img" aria-label="Glass mug of golden beer"></div>
  <div class="dish-label" style="left:143px;top:352px">Lorem ipsum</div>
  <div class="dish-label" style="left:331px;top:352px">Lorem ipsum</div>
  <div class="dish-label" style="left:690px;top:352px">Lorem ipsum</div>
  <div class="dish-label" style="left:877px;top:352px">Lorem ipsum</div>
  <div class="dish-label" style="left:510px;top:388px;font-size:17px">Lorem ipsum dolor</div>
  <p class="abs menu-desc">Sed ut perspiciatis unde omnis iste doloremque laudantium.</p>
  <div class="abs dots"><i></i><i class="on"></i><i></i></div>
  <svg class="tear" style="top:576px" viewBox="0 0 1200 24" preserveAspectRatio="none" aria-hidden="true"><use href="#edge" fill="#fdf8e3"/></svg>
</section>

<h2 class="abs section-title display blog-title">LATEST BLOG</h2>
<article class="abs card" style="left:144px">
  <div class="photo" style="background:linear-gradient(160deg,#d8d2c8,#7a6a5a 50%,#3a342e)" role="img" aria-label="Friends dancing at a party under string lights"></div>
  <span class="date">&#128197; Jan 25, 2023</span>
  <h3>Lorem ipsum dolor sit consectetur adipiscing elit, sed do</h3>
  <p>Sed ut perspiciatis unde omnis error sit voluptatem accusantium</p>
</article>
<article class="abs card" style="left:454px">
  <div class="photo" style="background:linear-gradient(160deg,#9ab0c0,#6a5a70 50%,#3a2e3a)" role="img" aria-label="Group celebrating outdoors at sunset"></div>
  <span class="date">&#128197; Jan 25, 2023</span>
  <h3>Lorem ipsum dolor sit consectetur adipiscing elit, sed do</h3>
  <p>Sed ut perspiciatis unde omnis error sit voluptatem accusantium</p>
</article>
<article class="abs card" style="left:765px">
  <div class="photo" style="background:linear-gradient(160deg,#bcd4ea,#b07050 55%,#4a3a2a)" role="img" aria-label="Friends sharing food and drinks on a terrace"></div>
  <span class="date">&#128197; Jan 25, 2023</span>
  <h3>Lorem ipsum dolor sit consectetur adipiscing elit, sed do</h3>
  <p>Sed ut perspiciatis unde omnis error sit voluptatem accusantium</p>
</article>

<section class="abs band testi-band">
  <svg class="tear" style="top:-12px;transform:scaleY(-1)" viewBox="0 0 1200 24" preserveAspectRatio="none" aria-hidden="true"><use href="#edge" fill="#fdf8e3"/></svg>
  <h2 class="abs section-title display testi-title">TESTIMONIALS</h2>
  <span class="quote" style="left:166px">&ldquo;</span>
  <span class="quote" style="left:478px">&ldquo;</span>
  <span class="quote" style="left:790px">&ldquo;</span>
  <div class="tcard" style="left:144px">"Lorem ipsum dolor sit amet, consectetur adipiscing elit, sed do eiusmod tempor incididunt ut labore et dolore magna aliqua. Ut enim ad minim veniam, quis nostrud exercitation ullamco laboris nisi ut aliquip ex ea commodo consequat.</div>
  <div class="tcard" style="left:456px">"Lorem ipsum dolor sit amet, consectetur adipiscing elit, sed do eiusmod tempor incididunt ut labore et dolore magna aliqua. Ut enim ad minim veniam, quis nostrud exercitation ullamco laboris nisi ut aliquip ex ea commodo consequat.</div>
  <div class="tcard" style="left:768px">"Lorem ipsum dolor sit amet, consectetur adipiscing elit, sed do eiusmod tempor incididunt ut labore et dolore magna aliqua. Ut enim ad minim veniam, quis nostrud exercitation ullamco laboris nisi ut aliquip ex ea commodo consequat.</div>
  <div class="author" style="left:227px"><i role="img" aria-label="Reviewer portrait"></i>Lorem ipsum</div>
  <div class="author" style="left:538px"><i role="img" aria-label="Reviewer portrait"></i>Lorem ipsum</div>
  <div class="author" style="left:852px"><i role="img" aria-label="Reviewer portrait"></i>Lorem ipsum</div>
  <svg class="tear" style="top:433px" viewBox="0 0 1200 24" preserveAspectRatio="none" aria-hidden="true"><use href="#edge" fill="#fdf8e3"/></svg>
</section>

<h2 class="abs section-title display gallery-title">GALLERY</h2>
<div class="abs gtile" style="left:144px;top:2967px;background:linear-gradient(#5a3a22,#1e1812)" role="img" aria-label="Pub dining room with framed memorabilia"></div>
<div class="abs gtile" style="left:375px;top:2967px;background:linear-gradient(#d8d0c4,#a8988a)" role="img" aria-label="Champagne glasses toasting"></div>
<div class="abs gtile" style="left:607px;top:2967px;background:linear-gradient(#5a6a8a,#7a4a22)" role="img" aria-label="Long bar counter with screens"></div>
<div class="abs gtile" style="left:838px;top:2967px;background:linear-gradient(#1e1414,#6a4a3a)" role="img" aria-label="Woman smiling with a drink in a bar"></div>
<div class="abs gtile" style="left:144px;top:3143px;background:linear-gradient(#c8a44a,#8a3a2a)" role="img" aria-label="Colourful bar interior"></div>
<div class="abs gtile" style="left:375px;top:3143px;background:linear-gradient(#6a4a8a,#5a3a22)" role="img" aria-label="Beer mugs on a table in purple light"></div>
<div class="abs gtile" style="left:607px;top:3143px;background:linear-gradient(#c8c4bc,#6a6a5a)" role="img" aria-label="Long table set for a dinner event"></div>
<div class="abs gtile" style="left:838px;top:3143px;background:linear-gradient(#8a2a1a,#3a1a12)" role="img" aria-label="Crowded pub at night"></div>

<footer class="abs contact">
  <svg class="tear" style="top:-12px;transform:scaleY(-1)" viewBox="0 0 1200 24" preserveAspectRatio="none" aria-hidden="true"><use href="#edge" fill="#fdf8e3"/></svg>
  <h2 class="abs section-title display contact-title">CONTACT US</h2>
  <div class="info" style="left:200px">
    <svg width="46" height="50" viewBox="0 0 46 50" fill="none" stroke="#c2622a" stroke-width="2.5"><path d="M23 40S10 26 10 17a13 13 0 0 1 26 0c0 9-13 23-13 23z"/><circle cx="23" cy="17" r="5"/><path d="M12 36 3 46h40l-9-10"/></svg>
    <div><b>LOCATION:</b>900 Lorem ipsum dolor sit amet,<br>consectetur adipiscing elit</div>
  </div>
  <div class="info" style="left:508px">
    <svg width="46" height="46" viewBox="0 0 24 24" fill="none" stroke="#c2622a" stroke-width="1.3"><path d="M6.6 10.8a15 15 0 0 0 6.6 6.6l2.2-2.2c.3-.3.7-.4 1-.2 1.1.4 2.3.6 3.6.6.6 0 1 .4 1 1V20c0 .6-.4 1-1 1A17 17 0 0 1 3 4c0-.6.4-1 1-1h3.5c.6 0 1 .4 1 1 0 1.3.2 2.5.6 3.6.1.3 0 .7-.2 1z"/><path d="M14 3a7 7 0 0 1 7 7M14 6.5a3.5 3.5 0 0 1 3.5 3.5"/></svg>
    <div style="padding-top:10px"><b>PHONE:</b>+1 888 888 8888</div>
  </div>
  <div class="info" style="left:716px">
    <svg width="48" height="38" viewBox="0 0 48 38" fill="none" stroke="#c2622a" stroke-width="2.5"><rect x="2" y="2" width="44" height="34"/><path d="M2 2l22 18L46 2M2 36l16-16M46 36 30 20"/></svg>
    <div style="padding-top:6px"><b>EMAIL:</b>info@Bramwell Corner Sports Pub.com</div>
  </div>
  <div class="field" style="left:186px;top:261px;width:401px;height:46px">Name</div>
  <div class="field" style="left:186px;top:322px;width:401px;height:46px">Email Address</div>
  <div class="field" style="left:186px;top:382px;width:401px;height:47px">Phone Number</div>
  <div class="field" style="left:609px;top:259px;width:406px;height:172px">Message</div>
  <div class="btn">SUBMIT NOW <svg width="13" height="13" viewBox="0 0 16 16"><circle cx="8" cy="8" r="7.5" fill="#fff"/><path d="M6 4.5 9.5 8 6 11.5" stroke="#3f5b2c" stroke-width="2" fill="none"/></svg></div>
  <div class="abs foot-line"></div>
  <p class="abs copy">Copyright 2023@ Bramwell Corner Sports Pub.com</p>
  <div class="abs foot-brand">Bramwell Corner Sports Pub</div>
  <div class="abs social" aria-label="Social links"><i></i><i></i><i></i><i></i></div>
</footer>

</body>
</html>
```